Lanternfield Drinks business cards

We need a business card design for our new logo. The company is modern, progressive, professional, yet approachable. The key products are ready to drink bottles and cans of coffee based beverages.
These cards will be a critical part of the first impression made by our sales organization, business development team, and all external facing personnel.
Card can be a vertical or horizontal orientation.

Target Market(s)

Customers, suppliers, business partners

Industry/Entity Type

Business

Contact Information for Business Card

Business cards should feature Company Name and Logo.

Font styles to use
Serif

Colors

Designer to choose colors to be used in the design.

Requirements
Must have
• Strong readability of Name, phone #, mobile number and email address.
• Job title, website url, Street Address, and other details can be secondary level readability.
Nice to have
• High impact, simplistic quality design.
• Ok to utilize the 'H in the box' separate from the company name

```html
<!DOCTYPE html>
<html lang="en">
<head>
<meta charset="utf-8">
<title>Lanternfield Drinks — Business Cards</title>
<link rel="stylesheet" href="https://fonts.googleapis.com/css2?family=Cinzel:wght@700&family=Lora:wght@400;600&display=swap">
<style>
  :root {
    --backdrop: #1c1c1c;
    --orange-deep: #f0622f;
    --orange-light: #f79a5c;
    --orange-mid: #f47a42;
    --gold: #f2b233;
    --white: #ffffff;
    --paper: #f6f6f6;
    --brand-red: #e8542a;
  }
  * { box-sizing: border-box; margin: 0; padding: 0; }
  html, body { width: 1200px; height: 864px; overflow: hidden; }
  body { background: var(--backdrop); position: relative; font-family: "Lora", Georgia, serif; }

  .card {
    position: absolute;
    width: 620px;
    height: 354px;
    overflow: hidden;
    box-shadow: 0 12px 30px rgba(0,0,0,.55);
  }

  .brand-name {
    font-family: "Cinzel", Georgia, serif;
    font-weight: 700;
    color: var(--brand-red);
    letter-spacing: 1px;
    text-align: center;
  }

  /* Back of card */
  .card-back {
    left: 480px; top: 56px;
    background: linear-gradient(135deg, var(--orange-light), var(--orange-deep) 60%, var(--orange-mid));
  }
  .card-back .brand-panel {
    position: absolute; left: 0; top: 50px;
    width: 250px; height: 200px;
    background: var(--white);
    display: flex; align-items: center; justify-content: center;
    padding: 0 24px;
  }
  .card-back .brand-name {
    font-size: 26px;
    line-height: 1.15;
  }
  .card-back .stripes { position: absolute; left: 258px; top: 50px; height: 200px; }
  .card-back .decor-square {
    position: absolute; left: 330px; top: 70px;
    width: 220px; height: 220px;
    border: 14px solid rgba(255,255,255,.12);
  }

  /* Front of card */
  .card-front {
    left: 110px; top: 456px;
    background: linear-gradient(180deg, var(--white), var(--paper));
  }
  .card-front .brand-mark {
    position: absolute; left: 30px; top: 60px;
    width: 300px; height: 230px;
    display: flex; flex-direction: column; align-items: center; justify-content: center; gap: 16px;
  }
  .card-front .brand-square {
    width: 110px; height: 110px;
    border: 10px solid var(--orange-mid);
  }
  .card-front .brand-name {
    font-size: 21px;
    white-space: nowrap;
  }
  .card-front .stripes { position: absolute; left: 352px; top: 80px; height: 190px; }
  .contact-panel {
    position: absolute; left: 374px; top: 80px;
    width: 246px; height: 190px;
    background: linear-gradient(135deg, var(--orange-deep), var(--orange-light));
    color: var(--white);
    padding: 18px 20px;
  }
  .person-name { font-family: "Cinzel", Georgia, serif; font-weight: 700; font-size: 16px; letter-spacing: .5px; }
  .person-title { font-size: 12px; margin-bottom: 18px; }
  .contact-list { list-style: none; font-size: 12px; line-height: 19px; }
  .contact-list li { display: flex; align-items: center; gap: 8px; white-space: nowrap; }
  .contact-list svg { width: 12px; height: 12px; flex: none; }
  .address {
    position: absolute; left: 352px; top: 286px;
    font-size: 12.5px; color: var(--gold);
    white-space: nowrap;
  }
</style>
</head>
<body>

  <section class="card card-back" aria-label="Card back">
    <div class="decor-square"></div>
    <div class="brand-panel"><span class="brand-name">Lanternfield<br>Drinks</span></div>
    <svg class="stripes" width="16" height="200" viewBox="0 0 16 200">
      <rect x="0" width="3" height="200" fill="var(--gold)"/>
      <rect x="6" width="3" height="200" fill="var(--gold)"/>
      <rect x="12" width="3" height="200" fill="var(--gold)"/>
    </svg>
  </section>

  <section class="card card-front" aria-label="Card front">
    <div class="brand-mark">
      <div class="brand-square"></div>
      <span class="brand-name">Lanternfield Drinks</span>
    </div>
    <svg class="stripes" width="16" height="190" viewBox="0 0 16 190">
      <rect x="0" width="3" height="190" fill="var(--gold)"/>
      <rect x="6" width="3" height="190" fill="var(--gold)"/>
      <rect x="12" width="3" height="190" fill="var(--gold)"/>
    </svg>
    <div class="contact-panel">
      <div class="person-name">DANIEL ORTWELL</div>
      <div class="person-title">Managing Director</div>
      <ul class="contact-list">
        <li><svg viewBox="0 0 12 12"><rect x=".5" y=".5" width="11" height="11" fill="none" stroke="#fff"/><path d="M3.5 3 L5 3 L5.5 5 L4.7 5.6 Q5.6 7.3 6.6 7.5 L7.2 6.7 L9 7.3 L9 8.8 Q5 9 3.3 4.2 Z" fill="#fff"/></svg>425.555.0142</li>
        <li><svg viewBox="0 0 12 12"><rect x=".5" y=".5" width="11" height="11" fill="none" stroke="#fff"/><rect x="4" y="2.5" width="4" height="7" rx=".6" fill="#fff"/></svg>206.555.0187</li>
        <li><svg viewBox="0 0 12 12"><rect x=".5" y=".5" width="11" height="11" fill="none" stroke="#fff"/><path d="M2.5 4 H9.5 V8.5 H2.5 Z M2.5 4 L6 6.6 L9.5 4" fill="none" stroke="#fff"/></svg>dan@lanternfielddrinks.com</li>
        <li><svg viewBox="0 0 12 12"><rect x=".5" y=".5" width="11" height="11" fill="none" stroke="#fff"/><circle cx="6" cy="6" r="3.2" fill="none" stroke="#fff"/><path d="M2.8 6 H9.2 M6 2.8 V9.2" stroke="#fff" stroke-width=".7"/></svg>www.lanternfielddrinks.com</li>
      </ul>
    </div>
    <div class="address">418 Harbor Ave. Millbrook, NY 12545</div>
  </section>

</body>
</html>
```